Business Card Design

WE are looking for a premium quality Business Cards for a Law Firm . Copies of our current business card is attached.

Contact Information for Business Card

xyz

```html
<!DOCTYPE html>
<html lang="en">
<head>
<meta charset="utf-8">
<title>Hartwell Lawyers – Business Cards</title>
<link rel="stylesheet" href="https://fonts.googleapis.com/css2?family=Cinzel:wght@600&family=Arimo:wght@400;700&display=swap">
<style>
  :root {
    --green: #0f3a26;
    --gold: #b8945a;
    --paper: #fbfbf9;
    --ink: #1d1d1b;
    --backdrop: #e9e7e3;
    --white: #ffffff;
  }
  * { box-sizing: border-box; margin: 0; padding: 0; }
  html, body { width: 1200px; height: 912px; overflow: hidden; }
  body {
    background: var(--backdrop);
    font-family: "Arimo", Arial, sans-serif;
    display: flex; flex-direction: column; align-items: center; justify-content: center; gap: 44px;
  }
  .card {
    width: 700px; height: 400px; position: relative; overflow: hidden;
    box-shadow: 0 6px 18px rgba(0,0,0,.18);
  }

  /* Shared wordmark: circle above, name below, centred */
  .brand {
    display: flex; flex-direction: column; align-items: center; gap: 14px;
    font-family: "Cinzel", Georgia, serif; font-weight: 600;
    white-space: nowrap;
  }
  .brand__circle { width: 72px; height: 72px; border-radius: 50%; border: 3px solid currentColor; flex: none; }
  .brand__name { font-size: 26px; letter-spacing: 1px; line-height: 1; }

  /* Front: offices */
  .card--offices { background: var(--green); color: var(--white); }
  .card--offices .brand { position: absolute; top: 42px; left: 50%; transform: translateX(-50%); color: var(--white); }
  .offices {
    position: absolute; left: 40px; right: 40px; bottom: 52px;
    display: grid; grid-template-columns: repeat(3, 1fr);
  }
  .office { text-align: center; font-size: 13px; line-height: 1.4; padding: 6px 0; }
  .office + .office { border-left: 1px solid rgba(255,255,255,.55); }
  .office__city { font-weight: 700; font-size: 15px; margin-bottom: 2px; }
  .office__phone b { font-weight: 700; }

  /* Back: personal */
  .card--personal { background: var(--paper); color: var(--ink); display: flex; }
  .card--personal .logo-side {
    width: 47%; flex: none; display: flex; align-items: center; justify-content: center; padding-bottom: 40px;
  }
  .card--personal .brand { color: var(--green); }
  .card--personal .brand__circle { border-color: var(--gold); }
  .divider { width: 1px; flex: none; background: #cfcfcf; margin: 40px 0 80px; }
  .details { padding: 44px 0 0 34px; font-size: 16px; line-height: 1.3; white-space: nowrap; }
  .person__name { font-family: "Cinzel", Georgia, serif; font-weight: 600; font-size: 24px; color: var(--green); }
  .person__title { color: var(--gold); font-size: 15px; margin-bottom: 12px; }
  .address { margin-bottom: 12px; }
  .contacts { list-style: none; }
  .contacts li { display: flex; align-items: center; gap: 10px; }
  .contacts svg { width: 14px; height: 14px; flex: none; }
  .rule-gold { position: absolute; left: 0; right: 0; bottom: 32px; height: 4px; background: var(--gold); }
  .band-green { position: absolute; left: 0; right: 0; bottom: 0; height: 26px; background: var(--green); }
</style>
</head>
<body>

<section class="card card--offices">
  <div class="brand">
    <span class="brand__circle"></span>
    <span class="brand__name">HARTWELL LAWYERS</span>
  </div>
  <div class="offices">
    <div class="office">
      <div class="office__city">Melbourne</div>
      <div>Level 12, 45 Market Lane</div>
      <div>Melbourne, VIC 3000</div>
      <div class="office__phone"><b>Phone :</b> +61 03 9000 1122</div>
    </div>
    <div class="office">
      <div class="office__city">Sydney</div>
      <div>Level 9, Rivergate Building</div>
      <div>22 Church Lane</div>
      <div>Parramatta, NSW 2150</div>
      <div class="office__phone"><b>Phone :</b> +61 02 8000 3344</div>
    </div>
    <div class="office">
      <div class="office__city">Perth</div>
      <div>Level 18, Quay Tower</div>
      <div>77 Bay Terrace</div>
      <div>Perth, WA 6000</div>
      <div class="office__phone"><b>Phone :</b> +61 08 6000 5566</div>
    </div>
  </div>
</section>

<section class="card card--personal">
  <div class="logo-side">
    <div class="brand">
      <span class="brand__circle"></span>
      <span class="brand__name">HARTWELL LAWYERS</span>
    </div>
  </div>
  <div class="divider"></div>
  <div class="details">
    <div class="person__name">DANIEL REYES</div>
    <div class="person__title">Director &amp; Principal Solicitor<br>MBA, Juris Doctor</div>
    <div class="address">Level 4, Harbour Chambers<br>212 Ridge Terrace<br>Spring Hill, QLD 4000</div>
    <ul class="contacts">
      <li><svg viewBox="0 0 16 16"><path fill="#0f3a26" d="M3 1l3 3-1.5 2a9 9 0 0 0 5.5 5.5L12 10l3 3-2 2C7 15 1 9 1 3z"/></svg>+61 7 3000 1234</li>
      <li><svg viewBox="0 0 16 16"><rect x="4" y="1" width="8" height="14" rx="1.5" fill="none" stroke="#0f3a26" stroke-width="1.6"/></svg>+61 0400 555 018</li>
      <li><svg viewBox="0 0 16 16"><rect x="1" y="3" width="14" height="10" fill="#0f3a26"/><path d="M1 3l7 6 7-6" fill="none" stroke="#fbfbf9" stroke-width="1.2"/></svg>daniel@hartwelllawyers.com.au</li>
      <li><svg viewBox="0 0 16 16"><circle cx="8" cy="8" r="7" fill="#0f3a26"/><path d="M1 8h14M8 1c-3 4-3 10 0 14M8 1c3 4 3 10 0 14" fill="none" stroke="#fbfbf9" stroke-width="1"/></svg>www.hartwelllawyers.com.au</li>
    </ul>
  </div>
  <div class="rule-gold"></div>
  <div class="band-green"></div>
</section>

</body>
</html>
```